Forensic Document Examiner, looking for contemporary update to my stationery design.

Looking for professional, classy logo design for stationery and business cards. My current stationery and business card is attached.I believe a logo image makes a header section interesting, so an intriguing design of a pen, feathered pen, microscope, magnifying glass, etc., would be appropriate. I have been in the business for over 30 years. I leave ideas to the imagination of the designer.My work involves mainly, the comparison of signatures and handwriting. I also resolve alterations, obliterations, and work as shown on my website: www.documentexaminer.infoThe image produced will be printed on quality white stationery and envelopes. The stationery will be photocopied by my clients, so the images should be reproducible. The business cards may be designed in other than white.

Target Market(s)

Attorneys

Font styles to use
Sans Serif

Colors

Designer to choose colors to be used in the design.

Requirements
Must have
• Image suitable for white stationery and photocopying.
• Classy logo and image; no casual fonts.
Nice to have
• Intriguing, contemporary design incorporating a relevant logo to my work.

```html
<!DOCTYPE html>
<html lang="en">
<head>
<meta charset="utf-8">
<title>Owen A. Hale — Letterhead</title>
<link href="https://fonts.googleapis.com/css2?family=Arimo:wght@400&family=Tinos:ital,wght@0,700;1,400&display=swap" rel="stylesheet">
<style>
  :root {
    --backdrop: #dfe2e4;
    --paper: #ffffff;
    --navy: #2b2a66;
    --rule-grey: #b9b9bb;
    --body-grey: #8a8a8e;
    --divider: #d9d9dc;
    --accent-yellow: #f3d64e;
    --signature-tint: #f1f1f3;
  }
  html, body {
    margin: 0;
    padding: 0;
    width: 1200px;
    height: 784px;
    overflow: hidden;
    background: var(--backdrop);
  }
  .letterhead {
    position: absolute;
    left: 338px;
    top: 22px;
    width: 524px;
    height: 740px;
    background: var(--paper);
    box-shadow: 0 2px 10px rgba(0,0,0,0.12);
    overflow: hidden;
  }
  .corner-tab {
    position: absolute;
    right: 34px;
    top: 0;
    width: 28px;
    height: 16px;
    background: var(--navy);
  }
  .header-rule {
    position: absolute;
    left: 0;
    top: 64px;
    width: 338px;
    height: 4px;
    background: var(--rule-grey);
    box-shadow: 0 3px 5px rgba(0,0,0,0.18);
  }
  .identity {
    position: absolute;
    left: 350px;
    top: 42px;
    display: flex;
    align-items: center;
    gap: 8px;
    white-space: nowrap;
  }
  .identity-dot {
    width: 14px;
    height: 14px;
    border-radius: 50%;
    background: var(--navy);
    flex: none;
  }
  .identity-name {
    font-family: "Tinos", "Times New Roman", serif;
    font-weight: 700;
    font-size: 17px;
    color: var(--navy);
    line-height: 1.1;
  }
  .identity-title {
    font-family: "Tinos", "Times New Roman", serif;
    font-style: italic;
    font-size: 9px;
    color: #6c6c78;
    margin-top: 2px;
  }
  .contact {
    position: absolute;
    right: 16px;
    top: 226px;
    margin: 0;
    padding: 0 0 0 12px;
    border-left: 1px solid var(--divider);
    font-family: "Tinos", "Times New Roman", serif;
    font-style: italic;
    font-size: 7.5px;
    color: var(--navy);
    list-style: none;
    white-space: nowrap;
  }
  .contact li {
    display: flex;
    align-items: center;
    gap: 5px;
    line-height: 13px;
  }
  .contact li::before {
    content: "";
    width: 6px;
    height: 6px;
    border-radius: 50%;
    background: var(--accent-yellow);
    flex: none;
  }
  .letter-body {
    position: absolute;
    left: 40px;
    top: 108px;
    width: 322px;
    font-family: "Arimo", Arial, sans-serif;
    font-size: 8px;
    line-height: 12.5px;
    color: var(--body-grey);
  }
  .letter-body p {
    margin: 0 0 13px;
    text-indent: 20px;
  }
  .signature {
    position: absolute;
    left: 40px;
    top: 430px;
    width: 150px;
    height: 48px;
    background: linear-gradient(90deg, var(--signature-tint), #fafafa);
  }
</style>
</head>
<body>
  <main class="letterhead">
    <div class="corner-tab"></div>
    <div class="header-rule"></div>

    <header class="identity">
      <span class="identity-dot"></span>
      <div>
        <div class="identity-name">Owen A. Hale</div>
        <div class="identity-title">Forensic Document Examiner</div>
      </div>
    </header>

    <ul class="contact">
      <li>PO Box 4182 Alder Falls, OR 97099</li>
      <li>555-014-2276</li>
      <li>ohale@quillmarkreview.info</li>
      <li>www.quillmarkreview.info</li>
    </ul>

    <section class="letter-body">
      <p>Lorem Ipsum is simply dummy text of the printing and typesetting industry. Lorem Ipsum has been the industry's standard dummy text ever since the 1500s, when an unknown printer took a galley of type and scrambled it to make a type specimen book. It has survived not only five centuries, but also the leap into electronic typesetting, remaining essentially unchanged. It was popularised in the 1960s with the release of transfer lettering sheets containing Lorem Ipsum passages, and more recently with desktop publishing software including versions of Lorem Ipsum.</p>
      <p>It is a long established fact that a reader will be distracted by the readable content of a page when looking at its layout. The point of using Lorem Ipsum is that it has a more-or-less normal distribution of letters, as opposed to using 'Content here, content here', making it look like readable English. Many desktop publishing packages and web page editors now use Lorem Ipsum as their default model text, and a search for 'lorem ipsum' will uncover many web sites still in their infancy. Various versions have evolved over the years, sometimes by accident, sometimes on purpose (injected humour and the like).</p>
      <p>Contrary to popular belief, Lorem Ipsum is not simply random text. It has roots in a piece of classical Latin literature from 45 BC, making it over 2000 years old. A Latin scholar looked up one of the more obscure Latin words, consectetur, from a Lorem Ipsum passage, and going through the cites of the word in classical literature, discovered the undoubtable source. Lorem Ipsum comes from sections 1.10.32 and 1.10.33 of "de Finibus Bonorum et Malorum" structures, to generate Lorem Ipsum which looks reasonable. The generated Lorem Ipsum is therefore always free from repetition, injected humour, or non-characteristic words etc.</p>
    </section>

    <div class="signature" role="img" aria-label="Handwritten signature of the sender"></div>
  </main>
</body>
</html>
```